Website Design for WestaKolory.pl – Luxury Wedding Car Rental with Chauffeur

We are looking for a talented designer to create a modern, elegant, and fully responsive website for our new brand – WestyKolory.pl. We are a premium car rental platform in Poland, offering luxury and exotic vehicles exclusively for weddings. All cars come with a professional chauffeur, ensuring a high-end, stress-free, and stylish experience.
Website Purpose:
The website should present our offering in a luxurious, clear, and inspiring way. It must build trust, highlight the prestige of our brand, and encourage inquiries. Our target audience includes engaged couples, wedding planners, and clients seeking a truly exceptional vehicle for their special day.
Design Requirements:
Style: modern, elegant, minimalist
Color palette: white, black, gold, optionally silver – refined and luxurious
Typography: clean, modern, high-end
Layout: clear, intuitive, with large car images and well-defined sections
Fully responsive (desktop, tablet, mobile)
Bilingual layout (Polish/English) must be considered
Pages to Design:
Homepage
About Us
Fleet Overview
Individual Car Pages
Services (Weddings, Photo Shoots, Film Rentals)
Why Us / Unique Selling Points
Contact
FAQ
Inspiration:
Luxury automotive brands (e.g. Varnel-Hoske, Corvash, Elbrin Tusko)
High-end wedding websites
Minimalist layouts with large visuals and elegant typography
Additional Notes:
The design should evoke the emotions of a wedding day – elegance, uniqueness, style, and class. Please avoid flashy colors, excessive graphic effects, or overly decorative elements. Subtlety, prestige, and sophistication are key.

```html
<!DOCTYPE html>
<html lang="en">
<head>
<meta charset="utf-8">
<title>WestaKolory.pl – Luxury Wedding Cars</title>
<link rel="stylesheet" href="https://fonts.googleapis.com/css2?family=Playfair+Display:wght@400;500;700&family=DM+Sans:wght@400;500;600&display=swap">
<style>
:root{
  --gold:#d4b34f;
  --navy:#131e2e;
  --ink:#111111;
  --text:#2a2a2a;
  --muted:#5a5a5a;
  --grey-band:#ebebeb;
  --rule:#d9d9d9;
  --white:#ffffff;
  --black:#000000;
}
*{box-sizing:border-box;margin:0;padding:0}
html,body{width:1200px;height:4383px;overflow:hidden}
body{position:relative;background:var(--white);font-family:"DM Sans",sans-serif;color:var(--text)}
.abs{position:absolute}
.heading{font-family:"Playfair Display",serif;font-weight:700;color:var(--navy);font-size:41px;line-height:1.15;white-space:nowrap}
.heading-mark{display:inline-block;width:50px;height:50px;border:2px solid var(--gold);border-radius:50%;vertical-align:middle;margin-left:8px;opacity:.8}
.btn{display:flex;align-items:center;gap:10px;justify-content:center;background:var(--gold);color:var(--navy);font-weight:600;font-size:16px;border-radius:26px;text-decoration:none}
.btn svg{width:16px;height:16px}
.photo{border-radius:14px}

/* hero */
.hero{left:0;top:0;width:1200px;height:601px;
  background:
    linear-gradient(180deg,rgba(12,18,28,.85) 0%,rgba(12,18,28,.35) 22%,rgba(0,0,0,0) 40%),
    linear-gradient(180deg,#2e3740 0%,#4a5458 20%,#3a4a34 32%,#5d8a3c 42%,#4f7c35 50%,#8e8472 62%,#a89a85 80%,#9c8f7c 100%)}
.logo{display:flex;align-items:center;gap:12px;font-family:"Playfair Display",serif;font-weight:400;font-size:34px;color:var(--gold)}
.logo-dot{width:18px;height:18px;border-radius:50%;background:var(--gold)}
.call{left:885px;top:8px;display:flex;align-items:center;gap:12px;color:var(--white);font-size:15px;font-weight:500}
.call-icon{width:42px;height:42px;border-radius:50%;background:var(--gold);display:flex;align-items:center;justify-content:center}
.nav{left:495px;top:68px;font-size:15px;font-weight:500;color:var(--white)}
.nav a{color:inherit;text-decoration:none;position:absolute;white-space:nowrap}
.nav a.active{color:var(--gold)}
.nav a.active::after{content:"";position:absolute;left:0;right:0;top:28px;height:2px;background:var(--gold)}
.hero-title{left:112px;top:200px;font-family:"Playfair Display",serif;font-weight:700;font-size:51px;color:var(--white);white-space:nowrap}
.hero-sub{left:112px;top:276px;width:370px;font-size:15px;line-height:24px;color:var(--white);font-weight:500}

/* about */
.about-art{left:68px;top:694px;width:504px;height:504px;border-radius:50%;background:radial-gradient(circle at 50% 42%,#c9ced4 0%,#6f7d8c 22%,#243447 48%,#152334 100%)}
.body-copy{font-size:15.5px;line-height:30px;color:var(--text);font-weight:500}

/* services */
.services{left:0;top:1277px;width:1200px;height:631px;background:var(--grey-band)}
.card-label{font-family:"Playfair Display",serif;font-size:26px;color:var(--navy);text-align:center;font-weight:500}

/* inspiration */
.insp-band{left:0;top:2560px;width:1200px;height:339px;background:var(--navy)}

/* faq */
.faq-q{font-size:19px;color:var(--ink);font-weight:400;line-height:25px}
.faq-a{font-size:12.5px;line-height:19px;color:var(--muted)}
.faq-icon{font-size:22px;color:var(--navy);font-weight:600}
.faq-rule{height:1px;background:var(--rule)}

/* footer */
.footer{left:0;top:3928px;width:1200px;height:455px;background:var(--black);color:var(--white)}
.footer h4{font-family:"Playfair Display",serif;font-weight:700;font-size:20px;letter-spacing:.5px}
.foot-links{font-size:14.5px;line-height:25.7px}
.contact-row{display:flex;gap:20px;font-size:14.5px;line-height:25px}
.contact-row svg{width:14px;height:14px;margin-top:6px;flex:none}
</style>
</head>
<body>

<!-- Hero -->
<section class="abs hero" role="img" aria-label="Classic silver and black luxury saloon parked on gravel before a green lawn and trees under a stormy sky"></section>
<div class="abs logo" style="left:112px;top:30px"><span class="logo-dot"></span>WestaKolory</div>
<div class="abs call">
  <span class="call-icon"><svg width="18" height="18" viewBox="0 0 24 24" fill="#131e2e"><path d="M6.6 10.8a15 15 0 0 0 6.6 6.6l2.2-2.2c.3-.3.7-.4 1-.2 1.1.4 2.3.6 3.6.6.6 0 1 .4 1 1V20c0 .6-.4 1-1 1A17 17 0 0 1 3 4c0-.6.4-1 1-1h3.5c.6 0 1 .4 1 1 0 1.3.2 2.5.6 3.6.1.3 0 .7-.2 1z"/></svg></span>
  Call Us : 512 300 718
</div>
<nav class="abs nav">
  <a class="active" style="left:0">Home</a>
  <a style="left:84px">About Us</a>
  <a style="left:191px">Fleet</a>
  <a style="left:267px">Services</a>
  <a style="left:370px">Why Us</a>
  <a style="left:463px">FAQ</a>
  <a style="left:536px">Contact</a>
</nav>
<h1 class="abs hero-title">Luxury Wedding Cars</h1>
<p class="abs hero-sub">Rent a Limousine or a Premium-class Van with a chauffeur</p>
<a class="abs btn" style="left:112px;top:349px;width:172px;height:50px">Explore Cars
  <svg viewBox="0 0 16 16"><circle cx="8" cy="8" r="8" fill="#131e2e"/><path d="M6 4.5 9.5 8 6 11.5" stroke="#d4b34f" stroke-width="2" fill="none"/></svg></a>

<!-- About -->
<div class="abs about-art" role="img" aria-label="Line illustration of a luxury saloon front view inside a dark navy circle"></div>
<h2 class="abs heading" style="left:648px;top:694px">About Us<span class="heading-mark"></span></h2>
<p class="abs body-copy" style="left:648px;top:763px;width:425px">WestyKolory.pl was created out of a genuine love for exceptional cars. We started as two young enthusiasts with a deep appreciation for vehicles that offer more than just performance – cars that create atmosphere, emotion, and presence. Over time, our private collection evolved into a premium chauffeur-driven service dedicated to weddings and refined celebrations.</p>
<p class="abs body-copy" style="left:648px;top:1033px;width:425px">Every car we offer is privately owned and maintained with the greatest care. We're not a typical rental company and never will be.</p>
<a class="abs btn" style="left:647px;top:1142px;width:174px;height:51px">Explore Cars
  <svg viewBox="0 0 16 16"><circle cx="8" cy="8" r="8" fill="#131e2e"/><path d="M6 4.5 9.5 8 6 11.5" stroke="#d4b34f" stroke-width="2" fill="none"/></svg></a>

<!-- Services -->
<section class="abs services"></section>
<h2 class="abs heading" style="left:0;width:1200px;text-align:center;top:1345px">Our Services<span class="heading-mark"></span></h2>
<div class="abs photo" style="left:111px;top:1445px;width:310px;height:333px;background:radial-gradient(ellipse at 35% 45%,#e8e4df 0%,#a39a91 30%,#3a3532 65%,#1c1a19 100%)" role="img" aria-label="Bride and groom smiling in the back seat of a wedding car"></div>
<div class="abs photo" style="left:444px;top:1445px;width:310px;height:333px;border:9px solid var(--gold);background:radial-gradient(ellipse at 50% 60%,#e6dccd 0%,#8d7560 35%,#3f5a2c 75%,#2e4420 100%)" role="img" aria-label="Couple embracing in a flower garden"></div>
<div class="abs photo" style="left:778px;top:1445px;width:310px;height:333px;background:radial-gradient(ellipse at 50% 50%,#f2f2f2 0%,#cfcfcf 40%,#7a7a7a 80%,#4a4a4a 100%)" role="img" aria-label="Empty white photo studio with lights"></div>
<div class="abs card-label" style="left:111px;width:310px;top:1785px">Weddings</div>
<div class="abs card-label" style="left:444px;width:310px;top:1785px">Photo Shoots</div>
<div class="abs card-label" style="left:778px;width:310px;top:1785px">Film Rentals</div>

<!-- Unique selling points -->
<h2 class="abs heading" style="left:116px;top:2018px">Unique Selling Points<span class="heading-mark"></span></h2>
<p class="abs body-copy" style="left:116px;top:2100px;width:425px">Sed ut perspiciatis unde omnis iste natus error sit voluptatem accusantium doloremque laudantium, totam rem aperiam, eaque ipsa quae ab illo inventore veritatis et quasi architecto beatae vitae dicta sunt explicabo. Nemo enim ipsam voluptatem quia voluptas sit aspernatur aut odit aut fugit, sed quia consequuntur magni dolores eos qui ratione voluptatem sequi nesciunt. Neque porro quisquam est, qui dolorem ipsum quia dolor sit amet,</p>
<a class="abs btn" style="left:116px;top:2401px;width:174px;height:51px">Explore Cars
  <svg viewBox="0 0 16 16"><circle cx="8" cy="8" r="8" fill="#131e2e"/><path d="M6 4.5 9.5 8 6 11.5" stroke="#d4b34f" stroke-width="2" fill="none"/></svg></a>
<svg class="abs" style="left:630px;top:1990px" width="490" height="470" viewBox="0 0 490 470">
  <circle cx="233" cy="236" r="228" fill="none" stroke="#d4b34f" stroke-width="2.5"/>
  <circle cx="240" cy="230" r="226" fill="none" stroke="#d4b34f" stroke-width="1.5"/>
</svg>
<div class="abs" style="left:640px;top:2003px;width:446px;height:446px;border-radius:50%;background:radial-gradient(ellipse at 55% 60%,#d9d2c2 0%,#7c7466 18%,#24282e 45%,#324a28 75%,#2a3d22 100%)" role="img" aria-label="Newlyweds kissing in front of a black luxury car in a park"></div>

<!-- Inspiration -->
<section class="abs insp-band"></section>
<h2 class="abs heading" style="left:0;width:1200px;text-align:center;top:2630px;color:var(--white)">Inspiration<span class="heading-mark"></span></h2>
<p class="abs" style="left:0;width:1200px;text-align:center;top:2716px;color:var(--white);font-size:16px;font-weight:500">Join our fans and clients community. Follow us and be up to date on new drops and discounts.</p>
<div class="abs photo" style="left:111px;top:2793px;width:230px;height:300px;background:radial-gradient(ellipse at 50% 65%,#b5aa9c 0%,#7d756b 35%,#3b3836 75%,#2a2827 100%)" role="img" aria-label="Bronze luxury SUV outside a showroom"></div>
<div class="abs photo" style="left:359px;top:2824px;width:230px;height:300px;background:radial-gradient(ellipse at 55% 40%,#dcc366 0%,#d3b54f 60%,#c9ab47 100%)" role="img" aria-label="Woman at an open car door under a gold overlay"></div>
<div class="abs photo" style="left:608px;top:2793px;width:230px;height:300px;background:linear-gradient(180deg,#eef1f4 0%,#b7c0c6 30%,#2a2d31 55%,#1b1d20 78%,#8f8f8c 100%)" role="img" aria-label="Chauffeur opening the door of a black saloon"></div>
<div class="abs photo" style="left:856px;top:2853px;width:230px;height:300px;background:linear-gradient(180deg,#d3d7da 0%,#8e969b 35%,#1e1f22 60%,#26272a 80%,#9a9a97 100%)" role="img" aria-label="Woman beside a black premium van"></div>

<!-- FAQ -->
<h2 class="abs heading" style="left:99px;top:3322px;font-size:42px;line-height:48px;color:var(--ink)">Frequently Asked<br>Questions</h2>
<div class="abs faq-q" style="left:102px;top:3456px">Do I need to book a chauffeur?</div>
<div class="abs" style="left:530px;top:3470px;width:12px;height:2px;background:var(--gold)"></div>
<p class="abs faq-a" style="left:102px;top:3499px;width:410px">Every car comes with a professional chauffeur, so you never drive yourself. Our drivers know the venues, plan the route in advance and arrive early, keeping your wedding day calm, punctual and perfectly on schedule.</p>
<div class="abs faq-rule" style="left:102px;top:3587px;width:440px"></div>
<div class="abs faq-q" style="left:102px;top:3610px">When should I book a wedding car?</div>
<div class="abs faq-icon" style="left:532px;top:3605px">+</div>
<div class="abs faq-rule" style="left:102px;top:3650px;width:440px"></div>
<div class="abs faq-q" style="left:102px;top:3668px;width:400px">What should I expect to pay for a wedding car?</div>
<div class="abs faq-icon" style="left:532px;top:3663px">+</div>
<div class="abs faq-rule" style="left:102px;top:3733px;width:440px"></div>
<div class="abs faq-q" style="left:102px;top:3751px">How do I get started?</div>
<div class="abs faq-icon" style="left:532px;top:3746px">+</div>
<div class="abs" style="left:621px;top:3278px;width:438px;height:514px;background:radial-gradient(ellipse at 45% 62%,#f4f3f0 0%,#d8d5cf 28%,#5a5652 55%,#2a2a2a 75%,#bcb8b1 100%)" role="img" aria-label="White wedding car decorated with ribbons and flowers"></div>
<div class="abs" style="left:1102px;top:3657px;width:3px;height:178px;background:var(--gold)"></div>
<div class="abs" style="left:914px;top:3832px;width:191px;height:3px;background:var(--gold)"></div>

<!-- Footer -->
<footer class="abs footer">
  <div class="abs logo" style="left:112px;top:170px;font-size:50px"><span class="logo-dot" style="width:26px;height:26px"></span>WestaKolory</div>
  <h4 class="abs" style="left:519px;top:90px">QUICK LINKS</h4>
  <div class="abs foot-links" style="left:523px;top:136px">Home<br>About Us<br>Fleet<br>Services<br>Why Us<br>FAQ<br>Contact</div>
  <h4 class="abs" style="left:791px;top:90px">GET IN TOUCH</h4>
  <div class="abs contact-row" style="left:803px;top:137px">
    <svg viewBox="0 0 24 24" fill="#fff"><path d="M12 2a7 7 0 0 0-7 7c0 5 7 13 7 13s7-8 7-13a7 7 0 0 0-7-7zm0 9.5A2.5 2.5 0 1 1 12 6.5a2.5 2.5 0 0 1 0 5z"/></svg>
    <span>Linden Court<br>London SE9 4QT, United Kingdom</span>
  </div>
  <div class="abs contact-row" style="left:803px;top:216px">
    <svg viewBox="0 0 24 24" fill="#fff"><path d="M6.6 10.8a15 15 0 0 0 6.6 6.6l2.2-2.2c.3-.3.7-.4 1-.2 1.1.4 2.3.6 3.6.6.6 0 1 .4 1 1V20c0 .6-.4 1-1 1A17 17 0 0 1 3 4c0-.6.4-1 1-1h3.5c.6 0 1 .4 1 1 0 1.3.2 2.5.6 3.6.1.3 0 .7-.2 1z"/></svg>
    <span>512 300 718</span>
  </div>
  <div class="abs contact-row" style="left:803px;top:278px">
    <svg viewBox="0 0 24 24" fill="#fff"><path d="M3 5h18v14H3z"/><path d="m3 6 9 7 9-7" stroke="#000" stroke-width="2" fill="none"/></svg>
    <span>hello@WestyKolory.pl</span>
  </div>
  <div class="abs" style="left:105px;top:353px;width:972px;height:1px;background:#8a8a8a"></div>
  <p class="abs" style="left:0;width:1200px;text-align:center;top:380px;font-size:14.5px">Copyright © 2025 WestyKolory.pl. All rights reserved.</p>
</footer>

</body>
</html>
```